Business Card Design

We are a residential half way house for the addict ,the alcoholic and dual diagnosed in recovery.
i house both men and woman age 18+

Industry/Entity Type

Residential

```html
<!DOCTYPE html>
<html lang="en">
<head>
<meta charset="utf-8">
<title>Harborlight Sober Living Residence — Business Card</title>
<link href="https://fonts.googleapis.com/css2?family=Arimo:wght@400&family=Ubuntu:wght@400;500&display=swap" rel="stylesheet">
<style>
  :root {
    --page-bg: #5a4634;
    --card-black: #0b0b0b;
    --card-sheen: #1c1c1c;
    --ink-white: #f4f4f4;
    --stripe-white: #e9e9e9;
    --divider: #cfcfcf;
  }
  * { box-sizing: border-box; margin: 0; padding: 0; }
  html, body {
    width: 1200px; height: 892px; overflow: hidden;
    background: var(--page-bg);
  }
  .canvas {
    position: relative; width: 1200px; height: 892px;
    display: flex; align-items: center; justify-content: center;
  }
  .business-card {
    position: relative; width: 1000px; height: 572px;
    background: linear-gradient(160deg, var(--card-sheen) 0%, var(--card-black) 45%, var(--card-black) 100%);
    color: var(--ink-white);
    font-family: "Arimo", Arial, sans-serif;
    box-shadow: 0 18px 40px rgba(0,0,0,0.45);
    overflow: hidden;
  }
  .owner-block {
    position: absolute; left: 110px; top: 150px; width: 300px;
    text-align: right;
  }
  .owner-name { font-size: 38px; font-weight: 400; letter-spacing: 0.5px; }
  .owner-role { font-size: 24px; margin-top: 4px; }
  .owner-note { font-size: 24px; margin-top: 14px; text-align: center; }
  .divider-vertical {
    position: absolute; width: 2px; background: var(--divider);
  }
  .divider-top { left: 445px; top: 140px; height: 150px; }
  .divider-contact { left: 560px; top: 368px; height: 118px; }
  .brand-block { position: absolute; left: 480px; top: 138px; }
  .brand-name {
    font-family: "Ubuntu", sans-serif; font-weight: 500;
    font-size: 62px; line-height: 1; letter-spacing: 0;
  }
  .brand-sub {
    font-family: "Ubuntu", sans-serif; font-weight: 400;
    font-size: 30px; margin-top: 12px;
  }
  .stripe {
    position: absolute; left: 0; width: 100%; height: 7px;
    background: var(--stripe-white);
  }
  .stripe-upper { top: 338px; }
  .stripe-lower { top: 508px; }
  .contact-address {
    position: absolute; left: 150px; top: 372px; width: 380px;
    text-align: right; font-size: 24px; line-height: 1.38;
  }
  .contact-phones {
    position: absolute; left: 595px; top: 366px;
    font-size: 25px; line-height: 1.4;
  }
  .phone-line { display: flex; align-items: center; gap: 12px; }
  .phone-icon { width: 22px; height: 22px; fill: var(--ink-white); }
</style>
</head>
<body>
<main class="canvas">
  <section class="business-card">
    <div class="owner-block">
      <p class="owner-name">Dana Whitfield</p>
      <p class="owner-role">Owner</p>
      <p class="owner-note">( House Manager )</p>
    </div>

    <span class="divider-vertical divider-top"></span>

    <div class="brand-block">
      <h1 class="brand-name">Harborlight</h1>
      <p class="brand-sub">Sober Living Residence</p>
    </div>

    <span class="stripe stripe-upper"></span>

    <div class="contact-address">
      <p>danawhitfield@examplemail.com</p>
      <p>2740 Palm Grove Rd.</p>
      <p>Harbor Point,Fla 33999</p>
    </div>

    <span class="divider-vertical divider-contact"></span>

    <div class="contact-phones">
      <p class="phone-line">
        <svg class="phone-icon" viewBox="0 0 24 24" aria-hidden="true"><path d="M3 8c0-2 2-4 9-4s9 2 9 4v2h-5V8H8v2H3z"/><rect x="5" y="12" width="14" height="9" rx="2"/></svg>
        (555) 201-0147
      </p>
      <p class="phone-line">
        <svg class="phone-icon" viewBox="0 0 24 24" aria-hidden="true"><path d="M3 8c0-2 2-4 9-4s9 2 9 4v2h-5V8H8v2H3z"/><rect x="5" y="12" width="14" height="9" rx="2"/></svg>
        (555) 201-0148
      </p>
      <p class="phone-line">
        <svg class="phone-icon" viewBox="0 0 24 24" aria-hidden="true"><rect x="7" y="2" width="10" height="7"/><rect x="2" y="9" width="20" height="9" rx="2"/><rect x="6" y="15" width="12" height="7"/></svg>
        (555) 318-2264
      </p>
    </div>

    <span class="stripe stripe-lower"></span>
  </section>
</main>
</body>
</html>
```